one side yoga classes, other side rental log cabin

I need a flyer to advertise yoga classes on a lake , and to describe the various styles of classes, and who they can benefit, Days Times .prices
Linked to it is a rental log cabin that can be rented privetly to families or Groups (8 max) www.kelverstonletsbay.com This also is rented to yoga teacher that would like to Hire Cabin and the Studio www.orvelinehaven.co.uk or
for Holistic weekends.

Teacher

```html
<!DOCTYPE html>
<html lang="en">
<head>
<meta charset="utf-8">
<title>Orveline – Lakeside Yoga &amp; Cabin Flyers</title>
<link rel="stylesheet" href="https://fonts.googleapis.com/css2?family=Almendra&family=Arimo:wght@400;700&family=Archivo+Narrow:wght@400&display=swap">
<style>
  :root {
    --stage: #2b2b2b;
    --plum: #3d1239;
    --band: #6e2b62;
    --ink: #2a1a22;
    --white: #ffffff;
    --rule: #8a6e78;
    --sky: #c9d6ea;
    --haze: #f3e6ee;
    --sun: #f5b37a;
    --glow: #fbe3d0;
    --teal: #14b3a3;
    --mauve-dark: #4a3d42;
    --mauve: #7a6a70;
    --lodge-band: #46625e;
    --lodge-text: #7fa39d;
    --cabin-red: #d0262c;
    --panel-edge: #a89a9f;
  }
  * { margin: 0; padding: 0; box-sizing: border-box; }
  html, body { width: 1200px; height: 1015px; overflow: hidden; }
  body { background: var(--stage); position: relative; font-family: "Arimo", Arial, sans-serif; color: var(--ink); }

  /* ---------- cabin flyer (behind) ---------- */
  .cabin-flyer { position: absolute; left: 200px; top: 256px; width: 949px; height: 673px; overflow: hidden; background: var(--teal); }
  .cabin-shapes { position: absolute; left: 0; top: 0; }
  .cabin-heading { position: absolute; right: 29px; top: 176px; font-size: 30px; font-weight: 700; color: var(--cabin-red); white-space: nowrap; }
  .cabin-copy { position: absolute; left: 612px; width: 300px; text-align: center; font-size: 16.5px; line-height: 23.5px; color: var(--ink); }
  .cabin-copy .accent { color: var(--cabin-red); }
  .lodge-prompt { position: absolute; left: 99px; top: 507px; font-size: 22px; color: var(--lodge-text); white-space: nowrap; }
  .lodge-phones { position: absolute; left: 22px; width: 588px; top: 561px; text-align: center; font-size: 29px; color: var(--white); white-space: nowrap; }
  .lodge-website { position: absolute; left: 22px; width: 588px; top: 607px; text-align: center; font-size: 22px; letter-spacing: 3px; color: var(--ink); white-space: nowrap; }
  .lodge-flourish { position: absolute; left: 721px; top: 640px; width: 86px; height: 1px; background: var(--cabin-red); }

  /* ---------- yoga flyer (front) ---------- */
  .yoga-flyer { position: absolute; left: 62px; top: 74px; width: 966px; height: 686px; overflow: hidden; background: var(--haze); }
  .flyer-topbar { position: absolute; left: 0; top: 0; width: 100%; height: 24px; background: var(--plum); }
  .hero-photo {
    position: absolute; left: 0; top: 24px; width: 100%; height: 510px;
    background:
      radial-gradient(ellipse 360px 250px at 190px 360px, rgba(245,170,110,.85), rgba(245,170,110,0) 70%),
      radial-gradient(ellipse 500px 170px at 50px 50px, rgba(150,180,225,.9), rgba(150,180,225,0) 70%),
      linear-gradient(90deg, rgba(255,255,255,0) 28%, rgba(255,248,250,.85) 55%, rgba(255,248,250,.7) 100%),
      linear-gradient(180deg, var(--sky) 0%, var(--haze) 30%, var(--glow) 60%, var(--sun) 100%);
  }
  .headline { position: absolute; left: 250px; width: 700px; text-align: center; font-family: "Almendra", serif; font-weight: 400; font-size: 50px; line-height: 1; color: var(--ink); letter-spacing: 1px; white-space: nowrap; }
  .headline-1 { top: 52px; }
  .headline-2 { top: 107px; }
  .studio-band { position: absolute; left: 210px; top: 173px; width: 756px; height: 31px; background: linear-gradient(90deg, rgba(110,43,98,0) 0%, var(--band) 12%, var(--band) 100%); }
  .studio-band span { position: absolute; left: 0; width: 736px; top: 4px; text-align: center; color: var(--white); font-size: 23.5px; white-space: nowrap; padding-left: 0; }
  .subtitle { position: absolute; left: 312px; top: 216px; font-size: 21.5px; white-space: nowrap; }

  .rule { position: absolute; height: 1px; background: var(--rule); }
  .rule-accent { position: absolute; height: 4px; background: var(--band); }
  .t { position: absolute; font-size: 18px; line-height: 1; white-space: nowrap; }
  .t.class-name, .t.price { font-weight: 700; }
  .t.note { font-size: 14.5px; }

  .footer-curve { position: absolute; left: 0; top: 0; }
  .footer-divider { position: absolute; left: 357px; top: 530px; width: 1px; height: 104px; background: rgba(255,255,255,.35); }
  .brand-name { position: absolute; left: 16px; top: 560px; width: 340px; text-align: center; font-size: 42px; letter-spacing: 6px; color: var(--white); }
  .address { position: absolute; left: 52px; top: 638px; font-size: 15.5px; color: var(--white); white-space: nowrap; }
  .phones { position: absolute; left: 394px; top: 553px; font-family: "Archivo Narrow", sans-serif; font-size: 41px; color: var(--white); white-space: nowrap; }
  .other-info { position: absolute; left: 395px; top: 609px; font-size: 15.5px; color: var(--white); white-space: nowrap; }
  .website { position: absolute; left: 395px; top: 632px; font-size: 18px; font-weight: 700; letter-spacing: 5.5px; color: var(--white); white-space: nowrap; }
</style>
</head>
<body>
  <aside class="cabin-flyer">
    <svg class="cabin-shapes" width="949" height="673" viewBox="0 0 949 673" aria-hidden="true">
      <defs>
        <linearGradient id="cabinBox" x1="0" y1="0" x2="1" y2="0">
          <stop offset="0" stop-color="#4a3d42"/>
          <stop offset="1" stop-color="#7a6a70"/>
        </linearGradient>
        <linearGradient id="cabinPanel" x1="0" y1="0" x2="0" y2="1">
          <stop offset="0" stop-color="#ffffff"/>
          <stop offset="0.6" stop-color="#f1ecee"/>
          <stop offset="1" stop-color="#d9d0d4"/>
        </linearGradient>
      </defs>
      <rect x="22" y="16" width="903" height="133" fill="#4a3d42"/>
      <path d="M655 149 H925 C895 230 890 330 930 430 C890 520 895 600 925 673 H605 C640 640 635 600 600 575 C630 545 640 520 655 500 Z" fill="url(#cabinPanel)"/>
      <path d="M925 300 C895 360 890 400 930 430 C890 520 895 600 925 673" fill="none" stroke="#a89a9f" stroke-width="6"/>
      <path d="M655 500 C640 520 630 545 600 575 C635 600 640 640 605 673" fill="none" stroke="#a89a9f" stroke-width="6"/>
      <rect x="22" y="504" width="588" height="40" fill="#46625e"/>
      <rect x="22" y="544" width="588" height="105" fill="url(#cabinBox)"/>
    </svg>
    <p class="cabin-heading">Lakeside Holidays</p>
    <p class="cabin-copy" style="top:309px">All the luxuries<br>and also<br>every comfort!</p>
    <p class="cabin-copy accent" style="top:400px">Sleeps groups up to<br>Families &amp; groups (8 max)</p>
    <p class="cabin-copy" style="top:494px">Ideal for yoga teachers for<br>any groups looking to<br>really relax and enjoy<br>a weekend of<br>meditation and yoga<br>in a studio suspended<br>over the lake itself</p>
    <div class="lodge-flourish"></div>
    <p class="lodge-prompt">For Lodge Availability, Contact Us Direct</p>
    <p class="lodge-phones">01632 960 418 • 07700 900 573</p>
    <p class="lodge-website">www.kelverstonletsbay.com</p>
  </aside>

  <main class="yoga-flyer">
    <div class="flyer-topbar"></div>
    <div class="hero-photo" role="img" aria-label="Photograph of a woman in a tree yoga pose silhouetted against a sunset over the lake shore"></div>

    <h1 class="headline headline-1">A Peaceful &amp; Tranquil Lakeside</h1>
    <p class="headline headline-2">Retreat In The Heart Of Norfolk</p>

    <div class="studio-band"><span style="left:140px;width:596px">THE CALM AND RELAXING LAKESIDE STUDIO</span></div>
    <p class="subtitle">One To One Bookings With Lifestyle Analysis</p>

    <section class="timetable">
      <div class="rule" style="left:310px;top:250px;width:573px"></div>
      <div class="rule-accent" style="left:310px;top:249px;width:103px"></div>
      <span class="t" style="left:319px;top:262px">TUESDAY :</span>
      <span class="t" style="left:428px;top:262px">8am - 9am</span>
      <span class="t class-name" style="left:599px;top:262px">Gentle Asana Class</span>
      <span class="t price" style="left:825px;top:262px">£6.00</span>

      <div class="rule" style="left:425px;top:295px;width:458px"></div>
      <span class="t" style="left:424px;top:304px">10.00 - 11.15 am</span>
      <span class="t class-name" style="left:600px;top:304px">Dru Yoga</span>
      <span class="t note" style="left:596px;top:323px">(recommended for back care)</span>
      <span class="t price" style="left:825px;top:304px">£7.00</span>

      <div class="rule" style="left:425px;top:342px;width:458px"></div>
      <span class="t" style="left:424px;top:347px">19.00 - 20.00</span>
      <span class="t class-name" style="left:601px;top:347px">Hatha Yoga</span>
      <span class="t note" style="left:601px;top:368px">(at Brackenfield Memorial Hall)</span>
      <span class="t price" style="left:825px;top:347px">£7.00</span>

      <span class="t note" style="left:427px;top:390px">No class on the first <b>tuesday</b> of every month.</span>

      <div class="rule" style="left:310px;top:414px;width:573px"></div>
      <div class="rule-accent" style="left:310px;top:413px;width:103px"></div>
      <span class="t" style="left:319px;top:426px">FRIDAY</span>
      <span class="t" style="left:415px;top:426px">: 10.00AM - 11.15</span>
      <span class="t class-name" style="left:604px;top:426px">Hatha Yoga</span>
      <span class="t price" style="left:824px;top:426px">£7.00</span>

      <div class="rule" style="left:310px;top:457px;width:573px"></div>
      <span class="t" style="left:318px;top:470px"><span style="font-size:14.5px">Last</span> SUNDAY&nbsp; :</span>
      <span class="t note" style="left:318px;top:490px">of each month</span>
      <span class="t" style="left:463px;top:470px">8.30 - 10.00</span>
      <span class="t class-name" style="left:604px;top:470px">Flow Yoga class</span>
      <span class="t price" style="left:818px;top:470px">£10.00</span>
    </section>

    <svg class="footer-curve" width="966" height="686" viewBox="0 0 966 686" aria-hidden="true">
      <defs>
        <linearGradient id="footerFill" x1="0" y1="0" x2="1" y2="0">
          <stop offset="0" stop-color="#4a1746"/>
          <stop offset="1" stop-color="#26082a"/>
        </linearGradient>
      </defs>
      <path d="M0 494 C 120 515 190 526 300 526 C 550 524 800 506 966 497 L966 686 L0 686 Z" fill="url(#footerFill)"/>
      <path d="M0 494 C 120 515 190 526 300 526 C 550 524 800 506 966 497" fill="none" stroke="rgba(255,255,255,.55)" stroke-width="2"/>
    </svg>

    <footer>
      <p class="brand-name">ORVELINE</p>
      <p class="address">7 Ashmere Lakes, Ashmere. AB12 3CD</p>
      <div class="footer-divider"></div>
      <p class="phones">01632 960 418 • 07700 900 573</p>
      <p class="other-info">For other workshops and retreats/ activities visit</p>
      <p class="website">www.orvelinehaven.co.uk</p>
    </footer>
  </main>
</body>
</html>
```